Brell Stone Company Business Cards

Front and Back Business Card - logo and text setup - cool design. I need workable photoshop or illustrator files so I can setup each employee card with design that is created
Updates

Hi everyone, thank you for the great entries. Please no more white and blue cards - there are so many already - black and silver only now please. thanks!

Target Market(s)

Construction Industry - Facility Managers

Industry/Entity Type

Construction

Contact Information for Business Card

I really like contemporary simplistic looks - clean neat....not opposed to seeing some black backrounds

Requirements
Must have
• Logo/website address with design on front only - www.brellstone-example.com (logo attached)
• Back:
• Name/Title/Company Address/Phone/email address
Nice to have
• Cool design
Should not have
• Nothing gimmicky like Fire or Water - since we are a Fire Protection company - it has all been done

```html
<!DOCTYPE html>
<html lang="en">
<head>
<meta charset="utf-8">
<title>Brell Stone Company Business Cards</title>
<link href="https://fonts.googleapis.com/css2?family=Lato:wght@400;700;900&display=swap" rel="stylesheet">
<style>
  :root {
    --backdrop: #1b1b1d;
    --card-dark: #141416;
    --silver: #b9bdc3;
    --silver-light: #d9dce0;
    --white: #ffffff;
    --ink: #141416;
    --text: #2a2a2a;
  }
  * { margin: 0; padding: 0; box-sizing: border-box; }
  html, body { width: 1200px; height: 912px; overflow: hidden; }
  body {
    background: var(--backdrop);
    font-family: "Lato", Arial, sans-serif;
    position: relative;
  }
  .card {
    position: absolute;
    width: 520px;
    height: 297px;
    overflow: hidden;
    box-shadow: 0 12px 30px rgba(0,0,0,0.6);
  }
  .card-front {
    left: 80px; top: 140px;
    background: var(--card-dark);
    border: 1px solid #2a2a2e;
  }
  .card-back {
    left: 600px; top: 470px;
    background: var(--white);
  }
  .brand-name {
    font-weight: 900;
    letter-spacing: -1px;
    line-height: 1;
    white-space: nowrap;
  }
  .brand-mark { width: 16px; height: 16px; background: var(--silver); }
  .card-front .brand {
    position: absolute;
    left: 0; right: 0; top: 108px;
    display: flex; align-items: center; justify-content: center; gap: 12px;
  }
  .card-front .brand-name { color: var(--white); font-size: 50px; }
  .card-front .website {
    position: absolute; left: 0; right: 0; bottom: 36px;
    text-align: center; color: var(--silver-light); font-size: 15px; letter-spacing: 0.5px;
  }
  .card-back .brand {
    position: absolute; left: 28px; top: 108px;
    display: flex; align-items: center; gap: 8px;
  }
  .card-back .brand-name { color: var(--ink); font-size: 34px; }
  .card-back .brand-mark { width: 11px; height: 11px; }
  .divider {
    position: absolute; left: 248px; top: 42px;
    width: 1px; height: 130px; background: var(--ink);
  }
  .contact {
    position: absolute; left: 268px; top: 36px;
    color: var(--text); font-size: 12.5px; line-height: 1.35;
  }
  .contact .person { color: var(--ink); font-weight: 700; font-size: 19px; line-height: 1.1; }
  .contact .role { font-size: 13px; margin-bottom: 10px; }
  .contact .address { margin-bottom: 8px; }
  .contact .line { display: flex; align-items: center; gap: 7px; }
  .contact .line svg { width: 11px; height: 11px; fill: var(--ink); }
  .swoosh { position: absolute; left: 0; top: 0; width: 520px; height: 297px; }
  .card-back .website {
    position: absolute; right: 40px; bottom: 22px;
    color: var(--silver-light); font-size: 14px; letter-spacing: 0.5px;
  }
</style>
</head>
<body>
  <section class="card card-front">
    <div class="brand">
      <span class="brand-name">Brell Stone</span>
      <span class="brand-mark"></span>
    </div>
    <p class="website">www.brellstone-example.com</p>
  </section>

  <section class="card card-back">
    <svg class="swoosh" viewBox="0 0 520 297" aria-hidden="true">
      <path d="M0 272 C200 252 380 216 520 192 L520 204 C380 229 200 264 0 282 Z" fill="var(--silver)"/>
      <path d="M0 282 C200 264 380 229 520 204 L520 210 C380 236 200 270 0 288 Z" fill="var(--white)"/>
      <path d="M0 288 C200 270 380 236 520 210 L520 297 L0 297 Z" fill="var(--card-dark)"/>
    </svg>
    <div class="brand">
      <span class="brand-name">Brell Stone</span>
      <span class="brand-mark"></span>
    </div>
    <div class="divider"></div>
    <div class="contact">
      <p class="person">Dana Rowe Whitfield</p>
      <p class="role">President</p>
      <p class="address">48 Harbor Lane<br>Millbrook, NY 10000</p>
      <p class="line">
        <svg viewBox="0 0 24 24"><path d="M6.6 10.8a15.1 15.1 0 0 0 6.6 6.6l2.2-2.2c.3-.3.7-.4 1-.2 1.1.4 2.3.6 3.6.6.6 0 1 .4 1 1V20c0 .6-.4 1-1 1A17 17 0 0 1 3 4c0-.6.4-1 1-1h3.5c.6 0 1 .4 1 1 0 1.3.2 2.5.6 3.6.1.3 0 .7-.2 1z"/></svg>
        (555) 014-2290
      </p>
      <p class="line">
        <svg viewBox="0 0 24 24"><path d="M2 5h20v14H2z M2 5l10 8 10-8" fill="var(--ink)" stroke="var(--white)" stroke-width="1.5"/></svg>
        info@brellstone-example.com
      </p>
    </div>
    <p class="website">www.brellstone-example.com</p>
  </section>
</body>
</html>
```